Bramwell Valley Hospital

We need a template for our hospital newsletter.

I am attaching what we did for December and also what we did for January. We like the January one better, but we need to keep the old style calendar.

I am also attaching the logo.

We need the document to be easily editable so that we can change the content month to month.

Industry/Entity Type

Hospital

```html
<!DOCTYPE html>
<html lang="en">
<head>
<meta charset="utf-8">
<title>Bramwell Valley Hospital Newsletter</title>
<link href="https://fonts.googleapis.com/css2?family=Arimo:wght@400;700&display=swap" rel="stylesheet">
<style>
:root{
  --blue:#1b3fc4;
  --navy:#1d2a78;
  --red:#d9230f;
  --grey:#e6e6e6;
  --text:#2b2b2b;
  --white:#ffffff;
}
*{margin:0;padding:0;box-sizing:border-box}
html,body{width:827px;height:1200px;overflow:hidden}
body{background:#f4f4f4;font-family:"Arimo",Arial,sans-serif;color:var(--text);position:relative}
.top-band{position:absolute;left:0;top:0;width:827px;height:30px;background:#000}
.page{position:absolute;left:28px;top:30px;width:760px;height:1170px;background:var(--white);overflow:hidden}
.masthead{height:78px;position:relative}
.brand{position:absolute;left:16px;top:18px;display:flex;align-items:center;gap:10px}
.brand-mark{width:40px;height:40px;border-radius:50%;background:var(--red)}
.brand-name{font-size:22px;font-weight:700;color:var(--navy)}
.contact{position:absolute;right:11px;top:27px;text-align:right;color:var(--blue);font-size:15.5px;line-height:22px}
.contact .phone{color:var(--red);font-size:17px}
.hero{height:228px;position:relative;background:linear-gradient(180deg,#0b2a8a 0%,#1d4fb8 45%,#8a6a5a 75%,#2d2f3a 100%)}
.hero .tagline{position:absolute;right:12px;top:10px;color:var(--white);font-size:16px;letter-spacing:.5px}
.issue-bar{height:28px;background:var(--red);color:var(--white);display:flex;align-items:center;position:relative;font-weight:700}
.issue-bar .issue{position:absolute;left:22px;font-size:14px}
.issue-bar .url{position:absolute;left:237px;font-size:15px}
.issue-bar .date{position:absolute;left:556px;font-size:12px}
.social{position:absolute;right:2px;top:2px;height:24px;width:102px;background:var(--white);display:flex;align-items:center;justify-content:center;gap:6px}
.social span{width:13px;height:13px;display:block}
.main{position:absolute;left:16px;top:364px;width:533px}
.sidebar{position:absolute;left:561px;top:344px;width:192px;height:830px;background:var(--grey)}
.sidebar h3{background:var(--blue);color:var(--white);text-align:center;font-size:17px;height:34px;line-height:34px;margin-top:0}
.sidebar p{text-align:center;font-size:12.3px;line-height:19.7px;padding:10px 6px}
h2{color:var(--blue);font-weight:400;font-size:19px;margin:14px 0 4px}
.main p{font-size:12.2px;line-height:19.7px;text-align:justify;margin-bottom:19.7px}
.main p.tight{margin-bottom:0}
.split{display:flex;gap:16px;margin-bottom:23px;width:524px}
.split p{width:296px;margin:0}
.photo{width:212px;height:105px;flex:none;background:linear-gradient(180deg,#0d2f92 0%,#2d58b6 50%,#7e6454 80%,#2e2e36 100%)}
.wide p{width:531px}
</style>
</head>
<body>
<div class="top-band"></div>
<div class="page">
  <header class="masthead">
    <div class="brand"><span class="brand-mark"></span><span class="brand-name">Bramwell Valley Hospital</span></div>
    <div class="contact">For questions or to schedule an appointment<br>call the Specialty Clinic at <span class="phone">(555)204-1187</span></div>
  </header>
  <section class="hero" role="img" aria-label="Hospital building entrance at dusk">
    <div class="tagline">CARING&nbsp; FOR OUR COMMUNITY</div>
  </section>
  <div class="issue-bar">
    <span class="issue">ISSUE : 01</span>
    <span class="url">www.bramwellvalleyhospital.org</span>
    <span class="date">29 JULY 2014</span>
    <div class="social"><span style="background:#1a6cb0"></span><span style="background:#3aa0d8"></span><span style="background:#3b5a9a"></span><span style="background:#3a9a3a"></span><span style="background:#f28a1a"></span></div>
  </div>

  <aside class="sidebar">
    <h3>TIPS CORNER</h3>
    <p>Dale Hartwell, CRNA, of Ridgefield Anesthetist Group provides Pain Management Injections in Millbrook at Bramwell Valley Hospital.</p>
  </aside>

  <main class="main">
    <h2>Managing Your Pain</h2>
    <p>Pain can be difficult to describe, even by those that deal with its impact every day. One reason is that people feel pain differently. Also, the amount of pain people can tolerate is varied. It can be throbbing or dull, constant or come and go. Pain impacts how you feel physically and emotionally. It can lessen your ability to care for yourself, work or maintain relationships. If you are in pain, it is important you discuss it with your doctor. There are many treatments available to help manage your pain.</p>
    <p>Your doctor may recommend physical therapy, exercise or even avoiding certain activities or foods. Medication can play an important role. Your primary care doctor may instruct you to take over the counter or order prescription medications for you.</p>
    <p class="tight">Many types of pain can be treated with injections. Epidural steroid injections are used for some types of back, neck, arm or leg pain. These injections can improve pain and function for several months or even longer. They can be repeated to maintain the benefits. Injections are also used to treat trigger points. In these cases, there is commonly a trigger point that is tender and when pressed. Pain radiates out from the trigger point. These injections can be used to treat certain types of neck, back, shoulder, hip, arm or hand pain. If you are currently traveling to have injections for pain management talk to your doctor about having those services provided in Millbrook.</p>

    <h2>Vascular Disease Among Leading Causes of Death in US</h2>
    <p style="margin-bottom:6px">Pain can be difficult to describe, even by those that deal with its impact every day. One reason is that people feel pain differently. Also, the amount of pain people can tolerate is varied. It can be throbbing or dull, constant or come and go. Pain impacts how you feel physically and emotionally. It can lessen your ability to care for yourself, work or maintain relationships. If you are in pain, it is important you discuss it with your doctor. There are many treatments available to help manage your pain.</p>
    <div class="split">
      <p>Your doctor may recommend physical therapy, exercise or even avoiding certain activities or foods. Medication can play an important role. Your primary care doctor may instruct you to take over the counter or order prescription medications for you.</p>
      <div class="photo" role="img" aria-label="Hospital entrance at night"></div>
    </div>
    <div class="wide">
      <p class="tight">Your doctor may recommend physical therapy, exercise or even avoiding certain activities or foods. Medication can play an important role. Your primary care doctor may instruct you to take over the counter or order prescription medications for you.</p>
      <p>Many types of pain can be treated with injections. Epidural steroid injections are used for some types of back, neck, arm or leg pain. These injections can improve pain and function for several months or even longer. They can be repeated to maintain the benefits. Injections are also used to treat trigger points. In these cases, there is commonly a trigger point that is tender and when pressed. Pain radiates out from the trigger point. These injections can be used to treat certain types of neck, back, shoulder, hip, arm or hand pain.</p>
    </div>
  </main>
</div>
</body>
</html>
```